Gobal construction supply company needs new business card design

I need a business card design for my global supply company using an existing logo. i will be looking to print these on rounded corner cards with the black background version of my logo on the back. on the front white background, my logo again and my simple details.

```html
<!DOCTYPE html>
<html lang="en">
<head>
<meta charset="utf-8">
<title>Meridian Build Supply – Business Card</title>
<link href="https://fonts.googleapis.com/css2?family=Open+Sans:wght@400;600;700&display=swap" rel="stylesheet">
<style>
  :root {
    --stage: #8f8c8a;
    --card-white: #f4f4f4;
    --card-black: #1b1b1b;
    --ink: #111111;
    --text-grey: #4a4a4a;
    --accent-red: #d50000;
    --paper-white: #ffffff;
  }
  * { margin: 0; padding: 0; box-sizing: border-box; }
  html, body {
    width: 1200px; height: 960px; overflow: hidden;
    background: var(--stage);
    font-family: "Open Sans", Arial, sans-serif;
  }
  .canvas { position: relative; width: 1200px; height: 960px; }

  .card {
    position: absolute;
    width: 600px; height: 343px;
    border-radius: 20px;
  }
  .card-front { left: 314px; top: 113px; background: var(--card-white); }
  .card-back  { left: 311px; top: 472px; background: var(--card-black); }

  .brand {
    position: absolute;
    display: flex; align-items: center; gap: 10px;
    font-weight: 700; letter-spacing: 0.2px; white-space: nowrap;
  }
  .brand-dot {
    width: 16px; height: 16px; border-radius: 50%;
    background: var(--accent-red); flex: none;
  }
  .card-front .brand {
    right: 36px; top: 108px;
    font-size: 17px; color: var(--ink);
  }
  .card-back .brand {
    left: 0; right: 0; top: 198px; justify-content: center;
    font-size: 22px; color: var(--paper-white);
  }

  .holder { position: absolute; left: 38px; top: 156px; }
  .holder-name { font-size: 20px; font-weight: 400; color: var(--ink); line-height: 26px; letter-spacing: 0.3px; }
  .holder-role { font-size: 13.5px; color: var(--accent-red); line-height: 18px; }

  .contact-list {
    position: absolute; left: 38px; top: 214px;
    list-style: none;
  }
  .contact-list li {
    display: flex; align-items: center; gap: 8px;
    height: 19px; font-size: 13px; color: var(--text-grey);
  }
  .contact-list svg { width: 15px; height: 13px; fill: var(--accent-red); flex: none; }

  .address {
    position: absolute; left: 277px; top: 273px;
    font-size: 13px; line-height: 19px; color: var(--text-grey);
    font-style: normal;
  }
</style>
</head>
<body>
<main class="canvas">

  <section class="card card-front" aria-label="Business card front">
    <div class="brand"><span class="brand-dot"></span>MERIDIAN BUILD SUPPLY</div>

    <div class="holder">
      <p class="holder-name">DANIEL REYES</p>
      <p class="holder-role">CEO/FOUNDER</p>
    </div>

    <ul class="contact-list">
      <li>
        <svg viewBox="0 0 16 16" aria-hidden="true"><path d="M3.5 1l2.5 3-1.5 2c1 2 3 4 5 5l2-1.5 3 2.5-1.5 2.5C8 15 1 8 1 2.5z"/></svg>
        555 214 7730
      </li>
      <li>
        <svg viewBox="0 0 16 16" aria-hidden="true"><path d="M4 0h8v16H4zM5.5 2v10h5V2zM7 13.2h2v1.4H7z" fill-rule="evenodd"/></svg>
        555 308 6142
      </li>
      <li>
        <svg viewBox="0 0 16 16" aria-hidden="true"><path d="M4 1h8v4H4zM1 6h14v7h-2.5v-3h-9v3H1zM4.5 11h7v4h-7z"/></svg>
        555 471 9025
      </li>
      <li>
        <svg viewBox="0 0 16 16" aria-hidden="true"><path d="M1 3h14v10H1zM2.5 4.5 8 9l5.5-4.5z" fill-rule="evenodd"/></svg>
        daniel@meridianbuild.com
      </li>
      <li>
        <svg viewBox="0 0 16 16" aria-hidden="true"><circle cx="8" cy="8" r="7"/></svg>
        www.meridianbuild.com
      </li>
    </ul>

    <address class="address">
      1420 Harbor View Road<br>
      Fairview, Oregon 97024
    </address>
  </section>

  <section class="card card-back" aria-label="Business card back">
    <div class="brand"><span class="brand-dot"></span>MERIDIAN BUILD SUPPLY</div>
  </section>

</main>
</body>
</html>
```